A new presentation to our clients

we are a Real Estate agency, our website is www.lumibrasa.com and it’s time to have a new, fashion and remarcable Business Card. we want to differentiate ourselves from other companies so we want a business card that differentiates us. we want the business card to impact our customers. in the competitive market that we have today, we have to be different and it is this difference that we seek

Target Market(s)

Real Estate Clients

Contact Information for Business Card

We search a totaly diferent card from the usual

Font styles to use
Sans Serif

Colors
e34197

Requirements
Must have
• Logo, adress, phone contact, e-mail, photo, and our website
Nice to have
• We would like to see a modern business card
Should not have
• Houses or building draws

```html
<!DOCTYPE html>
<html lang="en">
<head>
<meta charset="utf-8">
<title>Lumi Brasa — Business Card</title>
<link rel="stylesheet" href="https://fonts.googleapis.com/css2?family=Open+Sans:wght@400;600;700&display=swap">
<style>
  :root {
    --brand-pink: #e5246f;
    --card-dark: #1d1d1f;
    --page-bg: #2a2a2c;
    --text-light: #e8e8ea;
    --text-muted: #bdbdc2;
    --rule: #3c3c40;
    --white: #ffffff;
  }
  * { box-sizing: border-box; margin: 0; padding: 0; }
  html, body {
    width: 1200px;
    height: 900px;
    overflow: hidden;
    background: var(--page-bg);
    font-family: "Open Sans", Arial, sans-serif;
  }
  .stage {
    position: relative;
    width: 1200px;
    height: 900px;
  }
  .card {
    position: absolute;
    width: 560px;
    height: 320px;
    border-radius: 22px;
    box-shadow: 0 18px 40px rgba(0,0,0,0.45);
  }
  /* Front */
  .card--front {
    left: 150px;
    top: 110px;
    background: var(--brand-pink);
    display: flex;
    flex-direction: column;
    align-items: center;
    justify-content: center;
  }
  .card--front .brand-name {
    color: var(--white);
    font-size: 54px;
    font-weight: 600;
    letter-spacing: 0.5px;
    margin-top: 10px;
  }
  .tagline {
    color: #f8c6da;
    font-size: 13px;
    font-weight: 600;
    letter-spacing: 1.2px;
    margin-top: 46px;
  }
  /* Back */
  .card--back {
    left: 490px;
    top: 470px;
    background: var(--card-dark);
  }
  .card--back .brand-name {
    position: absolute;
    right: 40px;
    top: 36px;
    color: var(--brand-pink);
    font-size: 50px;
    font-weight: 600;
    letter-spacing: 0.5px;
  }
  .divider {
    position: absolute;
    left: 40px;
    right: 40px;
    top: 132px;
    height: 1px;
    background: var(--rule);
  }
  .person {
    position: absolute;
    left: 40px;
    top: 150px;
  }
  .person__name {
    color: var(--brand-pink);
    font-size: 19px;
    font-weight: 700;
    letter-spacing: 0.3px;
    line-height: 1.15;
  }
  .person__role {
    color: var(--text-light);
    font-size: 15px;
    line-height: 1.3;
  }
  .contact-list {
    list-style: none;
    margin-top: 10px;
  }
  .contact-list li {
    display: flex;
    align-items: center;
    gap: 8px;
    color: var(--text-light);
    font-size: 15px;
    line-height: 22px;
  }
  .contact-list svg {
    width: 13px;
    height: 13px;
    fill: var(--brand-pink);
    flex: none;
  }
  .address {
    position: absolute;
    right: 40px;
    top: 164px;
    text-align: right;
    color: var(--text-muted);
    font-size: 15px;
    line-height: 1.35;
  }
</style>
</head>
<body>
<main class="stage">
  <section class="card card--front">
    <div class="brand-name">Lumi Brasa</div>
    <div class="tagline">THE HOUSE OF YOUR DREAMS!</div>
  </section>

  <section class="card card--back">
    <div class="brand-name">Lumi Brasa</div>
    <div class="divider"></div>

    <div class="person">
      <div class="person__name">DANIEL MOREIRA</div>
      <div class="person__role">Managing Director</div>
      <ul class="contact-list">
        <li>
          <svg viewBox="0 0 16 16" aria-hidden="true"><path d="M3 1.5l3 .5 1 3-1.8 1.3a9 9 0 0 0 4.5 4.5L11 9l3 1 .5 3-2 1.5C6.5 14 2 9.5 1.5 3.5z"/></svg>
          (+351) 220 418 536
        </li>
        <li>
          <svg viewBox="0 0 16 16" aria-hidden="true"><path d="M4 1h8v4H4z"/><path d="M1 6h14v6h-3v3H4v-3H1zM5 10v4h6v-4z"/></svg>
          (+351) 220 418 539
        </li>
        <li>
          <svg viewBox="0 0 16 16" aria-hidden="true"><path d="M1 3h14v10H1zM2.5 4.5 8 9l5.5-4.5z" fill-rule="evenodd"/></svg>
          geral@lumibrasa.com
        </li>
        <li>
          <svg viewBox="0 0 16 16" aria-hidden="true"><circle cx="8" cy="8" r="7"/></svg>
          www.lumibrasa.com
        </li>
      </ul>
    </div>

    <address class="address" style="font-style: normal;">
      Rua das Oliveiras Altas, 148<br>
      4410-052, Vila Nova de Gaia
    </address>
  </section>
</main>
</body>
</html>
```